Logo, Web and Mobile Designs for enterprise social media platform

All the details are in the attached document, please start reading the scope document first which explains what is this project about and the details about the needed deliverables, after that please read the UI_Requirements document which will detail what is expected regarding the coded web version since this is a coded contest, it is very important that you meet the UI requirements or suggest something else but we will need to agree first before working on the coded version

Good Luck

Target Market(s)

Enterprise Social Media

Industry/Entity Type

Media

Coding

Coded - Design and coding required

Number of Pages Required

5+ page

Font styles to use
Sans Serif

Requirements
Must have
• All the must haves are listed in the scope document so please check before you start

```html
<!DOCTYPE html>
<html lang="en">
<head>
<meta charset="utf-8">
<title>Teamvale – Timeline</title>
<link href="https://fonts.googleapis.com/css2?family=Roboto:wght@400;500;700&display=swap" rel="stylesheet">
<style>
:root{
  --blue:#56b4e7;
  --blue-dark:#3f9fd6;
  --blue-btn:#4aa3dc;
  --green:#7fc242;
  --bg:#eef3f8;
  --card:#ffffff;
  --line:#dfe4e9;
  --text:#6b7075;
  --muted:#9aa1a7;
  --heading:#3a3f44;
  --link:#45a8e0;
  --badge:#e9573f;
  --mark:#c9d3db;
}
*{box-sizing:border-box;margin:0;padding:0}
html,body{width:1200px;height:2553px;overflow:hidden}
body{background:var(--bg);font-family:"Roboto",Arial,sans-serif;color:var(--text);position:relative;font-size:12px}
a{color:var(--link);text-decoration:none}
svg{display:block}

/* Header */
.site-header{position:absolute;left:0;top:0;width:1200px;height:82px;background:var(--blue)}
.brand{position:absolute;left:75px;top:24px;color:#fff;font-size:29px;font-weight:700;letter-spacing:2px}
.header-icons{position:absolute;left:286px;top:26px;display:flex;gap:18px}
.header-icon{position:relative;width:30px;height:28px}
.count-badge{position:absolute;right:-12px;top:-8px;background:var(--badge);color:#fff;font-size:10px;line-height:15px;padding:0 4px;border-radius:2px}
.search{position:absolute;left:465px;top:22px;width:408px;height:39px;background:#fff;border-radius:20px;display:flex;align-items:center;padding:0 14px 0 26px;font-size:12px;color:#888}
.search span{flex:1}
.search-divider{width:1px;height:24px;background:var(--line);margin-right:12px}
.auth-btn{position:absolute;top:24px;height:35px;color:#fff;font-size:13px;font-weight:500;display:flex;align-items:center;justify-content:center;gap:6px;border-radius:2px}
.auth-btn.signup{left:928px;width:81px;background:var(--green)}
.auth-btn.login{left:1023px;width:85px;background:var(--blue-btn)}

/* Profile card */
.profile-card{position:absolute;left:75px;top:104px;width:1050px;height:447px;background:var(--card);border:1px solid var(--line)}
.cover{position:absolute;left:13px;top:14px;width:1020px;height:353px;background:linear-gradient(135deg,#5c6b6e 0%,#8a7a63 35%,#b08a52 60%,#6aa0a0 100%)}
.cover-actions{position:absolute;right:32px;top:303px;display:flex;gap:6px}
.cover-btn{height:29px;padding:0 12px;background:#fff;font-size:11px;color:#555;display:flex;align-items:center;gap:6px}
.cover-btn.more{width:48px;justify-content:center;gap:3px}
.dot{width:6px;height:6px;border-radius:50%;background:#555}
.avatar{position:absolute;left:38px;top:280px;width:162px;height:147px;background:var(--blue);border:6px solid #fff;box-shadow:0 0 0 1px var(--line);display:flex;align-items:center;justify-content:center;color:#fff;font-size:22px;font-weight:700}
.profile-title{position:absolute;left:216px;top:386px}
.profile-title h1{font-size:15px;font-weight:500;color:var(--heading);letter-spacing:.3px}
.profile-title p{font-size:10px;font-style:italic;color:var(--muted);margin-top:4px}
.profile-tabs{position:absolute;left:567px;top:398px;display:flex;font-size:13px;color:#777}
.tab{position:relative;margin-right:28px;padding-bottom:24px}
.tab.active{color:var(--heading);font-weight:500}
.tab.active::after{content:"";position:absolute;left:0;right:0;bottom:0;height:3px;background:var(--blue)}
.tab.more{display:flex;gap:8px;align-items:flex-start}

/* Left column */
.about{position:absolute;left:75px;top:587px;width:254px}
.about h2{font-size:13px;font-weight:700;color:var(--heading);display:flex;align-items:center;gap:10px}
.about .tagline{font-size:10px;font-style:italic;color:var(--muted);margin-top:8px}
.about .bio{font-size:12px;line-height:20px;margin-top:10px;color:#666}
.about-list{list-style:none;margin-top:16px}
.about-list li{display:flex;align-items:center;gap:12px;font-size:11.5px;color:#666;margin-bottom:11px}
.media-card{position:absolute;left:75px;top:803px;width:254px;height:222px;background:var(--card);border:1px solid var(--line)}
.media-card-head{height:38px;border-bottom:1px solid var(--line);display:flex;align-items:center;gap:10px;padding-left:10px;font-size:11px;color:var(--link)}
.media-grid{display:grid;grid-template-columns:repeat(3,72px);gap:8px 5px;padding:13px 0 0 8px}
.media-tile{height:70px}

/* Center column */
.composer{position:absolute;left:347px;top:587px;width:506px;height:89px;background:var(--card);border:1px solid var(--line)}
.composer-tabs{display:flex;align-items:center;gap:16px;padding:12px 0 0 12px;font-size:10px;color:#555}
.composer-tab{display:flex;align-items:center;gap:6px}
.composer-sep{width:1px;height:14px;background:var(--line)}
.composer-input{position:absolute;left:10px;top:50px;width:486px;height:28px;border:1px solid var(--line);font-size:10px;color:#666;padding:8px 0 0 10px}

.post{position:absolute;left:347px;width:506px;background:var(--card);border:1px solid var(--line);padding:17px 17px 0}
.post-head{display:flex;gap:16px}
.post-avatar{width:55px;height:55px;background:var(--blue);color:#fff;font-size:9px;font-weight:700;display:flex;align-items:center;justify-content:center}
.post-meta{padding-top:8px;font-size:11px;color:#666}
.post-time{margin-top:8px;font-size:10.5px;color:#888;display:flex;align-items:center;gap:8px}
.post-media{margin-top:17px;height:225px}
.post-text{font-size:11.2px;line-height:22px;color:#8a8f94;margin:14px 0 20px}
.post-actions{display:flex;height:37px;margin:0 -17px;border-top:1px solid var(--line);font-size:11px;color:#888}
.action{flex:1;display:flex;align-items:center;justify-content:center;gap:7px;border-right:1px solid var(--line)}
.action:last-child{border-right:0;color:var(--link);font-weight:500;flex:.9}

.loading{position:absolute;left:540px;top:2349px;width:120px;text-align:center;font-size:12px;color:#888}
.loading svg{margin:0 auto 10px}

/* Right column */
.newsletter{position:absolute;left:870px;top:587px;width:255px;height:157px;background:var(--blue);padding:14px 13px;color:#fff}
.newsletter h3{font-size:13px;font-weight:500}
.newsletter p{font-size:10.5px;line-height:20px;margin-top:10px}
.newsletter-btn{margin-top:10px;height:36px;background:var(--blue-btn);display:flex;align-items:center;justify-content:center;font-size:14px;font-weight:500}
.suggest{position:absolute;left:870px;top:757px;width:255px;height:271px;background:var(--card);border:1px solid var(--line);padding:14px 10px}
.suggest h3{font-size:12px;font-weight:700;color:var(--heading)}
.suggest h3 a{font-size:9px;font-weight:400}
.suggest-list{list-style:none;margin-top:14px}
.suggest-item{display:flex;align-items:flex-start;gap:12px;height:43px}
.suggest-mark{width:24px;height:24px;border-radius:50%;margin-top:1px;background:var(--mark)}
.suggest-name{font-size:12px;color:#444;display:flex;align-items:center;gap:7px}
.suggest-handle{font-size:9px;color:#888;margin-top:2px}
.video-card{position:absolute;left:870px;width:255px;background:var(--card);border:1px solid var(--line);padding:11px}
.video-thumb{position:relative;height:157px;display:flex;align-items:center;justify-content:center}
.video-card p{font-size:11px;line-height:22px;color:#888;margin-top:10px}

/* Footer */
.site-footer{position:absolute;left:0;top:2468px;width:1200px;height:85px;background:var(--blue);color:#fff}
.copyright{position:absolute;left:75px;top:34px;font-size:11px}
.footer-social{position:absolute;left:948px;top:22px;display:flex;gap:14px}
.social-circle{width:37px;height:37px;border:2px solid #fff;border-radius:50%}
.footer-code{position:absolute;right:57px;top:68px;font-size:9px}
</style>
</head>
<body>

<header class="site-header">
  <div class="brand">TEAMVALE</div>
  <div class="header-icons">
    <div class="header-icon">
      <svg width="30" height="24" viewBox="0 0 30 24"><circle cx="11" cy="7" r="5" fill="#2a8ac4"/><path d="M1 22c0-6 4-9 10-9s10 3 10 9z" fill="#2a8ac4"/><circle cx="21" cy="8" r="4" fill="#2a8ac4"/><path d="M19 14c6 0 10 2 10 8h-6c0-4-1-6-4-8z" fill="#2a8ac4"/></svg>
    </div>
    <div class="header-icon">
      <svg width="28" height="24" viewBox="0 0 28 24"><path d="M3 3h18a2 2 0 0 1 2 2v10a2 2 0 0 1-2 2H10l-6 5v-5H3a2 2 0 0 1-2-2V5a2 2 0 0 1 2-2z" fill="#2a8ac4"/></svg>
      <span class="count-badge">33</span>
    </div>
    <div class="header-icon">
      <svg width="26" height="26" viewBox="0 0 26 26"><circle cx="13" cy="13" r="11" fill="#2a8ac4"/><path d="M6 9c3 0 4 2 6 2s2 3 0 4-2 4-4 5M16 4c0 3 2 4 4 4s3 3 2 6" stroke="#56b4e7" stroke-width="2" fill="none"/></svg>
      <span class="count-badge">15</span>
    </div>
  </div>
  <div class="search"><span>Search</span><i class="search-divider"></i>
    <svg width="14" height="14" viewBox="0 0 14 14"><circle cx="6" cy="6" r="4.5" stroke="#444" stroke-width="1.8" fill="none"/><path d="M9.5 9.5l3.5 3.5" stroke="#444" stroke-width="1.8"/></svg>
  </div>
  <div class="auth-btn signup">
    <svg width="12" height="12" viewBox="0 0 12 12"><path d="M1 5h6V2l5 4-5 4V7H1z" fill="#fff"/></svg>SIGN UP</div>
  <div class="auth-btn login">
    <svg width="11" height="12" viewBox="0 0 11 12"><rect x="1" y="5" width="9" height="7" fill="#fff"/><path d="M3 5V3.5a2.5 2.5 0 0 1 5 0V5" stroke="#fff" stroke-width="1.5" fill="none"/></svg>LOGIN</div>
</header>

<section class="profile-card">
  <div class="cover" role="img" aria-label="Cover photo: hands holding phones and tablets over a table of social media icons"></div>
  <div class="cover-actions">
    <div class="cover-btn"><svg width="11" height="11" viewBox="0 0 11 11"><path d="M0 5h2v6H0zM3 5l3-5c1 0 2 1 1 3h3.5l-1 8H3z" fill="#555"/></svg>Like</div>
    <div class="cover-btn"><svg width="10" height="10" viewBox="0 0 10 10"><path d="M4 0h2v4h4v2H6v4H4V6H0V4h4z" fill="#555"/></svg>Follow</div>
    <div class="cover-btn"><svg width="11" height="11" viewBox="0 0 11 11"><circle cx="9" cy="2" r="2" fill="#555"/><circle cx="2" cy="5.5" r="2" fill="#555"/><circle cx="9" cy="9" r="2" fill="#555"/><path d="M9 2L2 5.5 9 9" stroke="#555" fill="none"/></svg>Share</div>
    <div class="cover-btn more"><i class="dot"></i><i class="dot"></i><i class="dot"></i></div>
  </div>
  <div class="avatar">Teamvale</div>
  <div class="profile-title">
    <h1>WELCOME TO TEAMVALE</h1>
    <p>Lorem Ipsum is simply dummy text</p>
  </div>
  <nav class="profile-tabs">
    <span class="tab active">Timeline</span>
    <span class="tab">Post text/files</span>
    <span class="tab">Comment</span>
    <span class="tab">Share</span>
    <span class="tab">Like</span>
    <span class="tab more">More <svg width="9" height="9" viewBox="0 0 9 9"><path d="M0 2h9L4.5 7z" fill="#777"/></svg></span>
  </nav>
</section>

<aside class="about">
  <h2>SOCIAL MEDIA PLATFORM
    <svg width="20" height="20" viewBox="0 0 20 20"><circle cx="10" cy="10" r="10" fill="var(--blue)"/><path d="M5.5 10l3 3 6-6" stroke="#fff" stroke-width="2" fill="none"/></svg>
  </h2>
  <p class="tagline">Lorem Ipsum is simply dummy text</p>
  <p class="bio">Connecting the world's professionals to make them more productive and successful. For Cus Service questions, tweet <a>@teamvale.com</a></p>
  <ul class="about-list">
    <li><svg width="10" height="14" viewBox="0 0 10 14"><path d="M5 0a5 5 0 0 1 5 5c0 4-5 9-5 9S0 9 0 5a5 5 0 0 1 5-5z" fill="#888"/><circle cx="5" cy="5" r="2" fill="#fff"/></svg>Lorem Ipsum Dummy Locations</li>
    <li><svg width="13" height="13" viewBox="0 0 13 13"><path d="M5 8l3-3M4 6L2 8a2 2 0 0 0 3 3l2-2M9 7l2-2a2 2 0 0 0-3-3L6 4" stroke="#888" stroke-width="1.5" fill="none"/></svg><a>www.teamvale.com</a></li>
    <li><svg width="12" height="12" viewBox="0 0 12 12"><rect x="0.5" y="1.5" width="11" height="10" stroke="#888" fill="none"/><path d="M0 4h12M3 0v3M9 0v3" stroke="#888"/></svg>Joined October 2015</li>
  </ul>
</aside>

<section class="media-card">
  <div class="media-card-head">
    <svg width="13" height="11" viewBox="0 0 13 11"><path d="M0 2h3l1-2h5l1 2h3v9H0z" fill="#888"/><circle cx="6.5" cy="6" r="2.5" fill="#fff"/></svg>1,052 Photo and Videos
  </div>
  <div class="media-grid">
    <div class="media-tile" role="img" aria-label="Photo: hand tapping network icons" style="background:linear-gradient(135deg,#1d2d3a,#5a7d96)"></div>
    <div class="media-tile" role="img" aria-label="Photo: colourful app icons" style="background:linear-gradient(135deg,#1a3c6e,#e8a43a)"></div>
    <div class="media-tile" role="img" aria-label="Photo: world map of connections" style="background:linear-gradient(135deg,#2f7cbf,#8dc3e6)"></div>
    <div class="media-tile" role="img" aria-label="Photo: network of people icons" style="background:linear-gradient(135deg,#2a7dbf,#5fb2e0)"></div>
    <div class="media-tile" role="img" aria-label="Photo: social media icons collage" style="background:linear-gradient(135deg,#f2f2f2,#8fbde0)"></div>
    <div class="media-tile" role="img" aria-label="Photo: tree of icons on yellow" style="background:linear-gradient(135deg,#f6d21d,#e9b910)"></div>
  </div>
</section>

<section class="composer">
  <div class="composer-tabs">
    <span class="composer-tab"><svg width="12" height="12" viewBox="0 0 12 12"><rect width="12" height="12" fill="#e9c46a"/><path d="M2 4h8M2 7h6" stroke="#fff"/></svg>Status</span>
    <i class="composer-sep"></i>
    <span class="composer-tab"><svg width="12" height="12" viewBox="0 0 12 12"><rect width="12" height="12" fill="#8a6d4f"/><circle cx="6" cy="6" r="3" fill="#fff"/></svg>Photos</span>
    <i class="composer-sep"></i>
    <span class="composer-tab"><svg width="10" height="13" viewBox="0 0 10 13"><path d="M5 0a5 5 0 0 1 5 5c0 3-5 8-5 8S0 8 0 5a5 5 0 0 1 5-5z" fill="#e05a4f"/></svg>Place</span>
    <i class="composer-sep"></i>
    <svg width="100" height="10" viewBox="0 0 100 10"><circle cx="4" cy="5" r="3.5" fill="#777"/><path d="M22 2h7v6h-7z" fill="#777"/><path d="M44 9l4-8 4 8z" fill="#777"/><circle cx="70" cy="5" r="3.5" fill="#777"/><path d="M88 1l8 4-8 4z" fill="#777"/></svg>
  </div>
  <div class="composer-input">What's on Your mind?</div>
</section>

<article class="post" style="top:691px">
  <div class="post-head">
    <div class="post-avatar">Teamvale</div>
    <div class="post-meta"><a>It is a long established</a> fact that a reader when <a>https://teamvale.net/</a>
      <div class="post-time">3 minutes ago <svg width="9" height="9" viewBox="0 0 9 9"><circle cx="4.5" cy="4.5" r="4.5" fill="#888"/></svg></div></div>
  </div>
  <div class="post-media" role="img" aria-label="Photo: laptop on a desk showing the words social media, surrounded by notes and pencils" style="background:linear-gradient(120deg,#7a5a3c 0%,#d9c6a6 40%,#f4f1ec 55%,#a47c53 100%)"></div>
  <p class="post-text">It is a long established fact that a reader will be distracted by the readable content of a page when looking at its layout. The point of using Lorem Ipsum is that it has a more-or-less as opposed to using 'like readable English.<a>[......]</a></p>
  <div class="post-actions">
    <span class="action">↩ Repaly</span><span class="action">⇄ Retweet</span><span class="action">♥ Likes</span><span class="action">▭ Comments</span><span class="action">••• More</span><span class="action">VIEW MORE</span>
  </div>
</article>

<article class="post" style="top:1161px">
  <div class="post-head">
    <div class="post-avatar">Teamvale</div>
    <div class="post-meta"><a>It is a long established</a> fact that a reader when <a>https://teamvale.net/</a>
      <div class="post-time">3 minutes ago <svg width="9" height="9" viewBox="0 0 9 9"><circle cx="4.5" cy="4.5" r="4.5" fill="#888"/></svg></div></div>
  </div>
  <div class="post-media" role="img" aria-label="Illustration: megaphone spraying colourful social media icons" style="background:linear-gradient(90deg,#eef3f6 0%,#f6b13c 25%,#49a8dc 50%,#e85a8a 75%,#f2f2f2 100%)"></div>
  <p class="post-text">It is a long established fact that a reader will be distracted by the readable content of a page when looking at its layout. The point of using Lorem Ipsum is that it has a more-or-less as opposed to using 'like readable English.<a>[......]</a></p>
  <div class="post-actions">
    <span class="action">↩ Repaly</span><span class="action">⇄ Retweet</span><span class="action">♥ Likes</span><span class="action">▭ Comments</span><span class="action">••• More</span><span class="action">VIEW MORE</span>
  </div>
</article>

<article class="post" style="top:1627px">
  <div class="post-head">
    <div class="post-avatar">Teamvale</div>
    <div class="post-meta"><a>It is a long established</a> fact that a reader when <a>https://teamvale.net/</a>
      <div class="post-time">3 minutes ago <svg width="9" height="9" viewBox="0 0 9 9"><circle cx="4.5" cy="4.5" r="4.5" fill="#888"/></svg></div></div>
  </div>
  <p class="post-text">It is a long established fact that a reader will be distracted by the readable content of a page when looking at its layout. The point of using Lorem Ipsum is that it has a more-or-less as opposed to using 'like readable English.<a>[......]</a></p>
  <div class="post-actions">
    <span class="action">↩ Repaly</span><span class="action">⇄ Retweet</span><span class="action">♥ Likes</span><span class="action">▭ Comments</span><span class="action">••• More</span><span class="action">VIEW MORE</span>
  </div>
</article>

<article class="post" style="top:1855px">
  <div class="post-head">
    <div class="post-avatar">Teamvale</div>
    <div class="post-meta"><a>It is a long established</a> fact that a reader when <a>https://teamvale.net/</a>
      <div class="post-time">3 minutes ago <svg width="9" height="9" viewBox="0 0 9 9"><circle cx="4.5" cy="4.5" r="4.5" fill="#888"/></svg></div></div>
  </div>
  <div class="post-media" role="img" aria-label="Illustration: 3D words social media with floating app icons and clouds" style="background:linear-gradient(135deg,#d9dcd8 0%,#f1f2ef 45%,#8fc64a 65%,#2f8fcf 85%,#dfe2e0 100%)"></div>
  <p class="post-text">It is a long established fact that a reader will be distracted by the readable content of a page when looking at its layout. The point of using Lorem Ipsum is that it has a more-or-less as opposed to using 'like readable English.<a>[......]</a></p>
  <div class="post-actions">
    <span class="action">↩ Repaly</span><span class="action">⇄ Retweet</span><span class="action">♥ Likes</span><span class="action">▭ Comments</span><span class="action">••• More</span><span class="action">VIEW MORE</span>
  </div>
</article>

<div class="loading">
  <svg width="50" height="50" viewBox="0 0 50 50">
    <circle cx="25" cy="5" r="3.5" fill="#333"/><circle cx="39" cy="11" r="3.2" fill="#555"/><circle cx="45" cy="25" r="3" fill="#777"/><circle cx="39" cy="39" r="2.8" fill="#999"/><circle cx="25" cy="45" r="2.6" fill="#aaa"/><circle cx="11" cy="39" r="2.4" fill="#bbb"/><circle cx="5" cy="25" r="2.2" fill="#ccc"/><circle cx="11" cy="11" r="2" fill="#ddd"/>
  </svg>
  Loading......
</div>

<aside class="newsletter">
  <h3>NEWSLETTER SIGN UP</h3>
  <p>Sign up now to get your own personalised timeline!</p>
  <div class="newsletter-btn">SIGN UP</div>
</aside>

<aside class="suggest">
  <h3>YOU MAY ALSO LIKE . <a>Refresh</a></h3>
  <ul class="suggest-list">
    <li class="suggest-item"><i class="suggest-mark"></i><div><div class="suggest-name">Orbitra <svg width="11" height="11" viewBox="0 0 20 20"><circle cx="10" cy="10" r="10" fill="var(--blue)"/><path d="M5.5 10l3 3 6-6" stroke="#fff" stroke-width="2.5" fill="none"/></svg></div><div class="suggest-handle">@orbitra</div></div></li>
    <li class="suggest-item"><i class="suggest-mark"></i><div><div class="suggest-name">Nestwave <svg width="11" height="11" viewBox="0 0 20 20"><circle cx="10" cy="10" r="10" fill="var(--blue)"/><path d="M5.5 10l3 3 6-6" stroke="#fff" stroke-width="2.5" fill="none"/></svg></div><div class="suggest-handle">@nestwave</div></div></li>
    <li class="suggest-item"><i class="suggest-mark"></i><div><div class="suggest-name">Brightloop <svg width="11" height="11" viewBox="0 0 20 20"><circle cx="10" cy="10" r="10" fill="var(--blue)"/><path d="M5.5 10l3 3 6-6" stroke="#fff" stroke-width="2.5" fill="none"/></svg></div><div class="suggest-handle">@brightloop</div></div></li>
    <li class="suggest-item"><i class="suggest-mark"></i><div><div class="suggest-name">Maplecrest <svg width="11" height="11" viewBox="0 0 20 20"><circle cx="10" cy="10" r="10" fill="var(--blue)"/><path d="M5.5 10l3 3 6-6" stroke="#fff" stroke-width="2.5" fill="none"/></svg></div><div class="suggest-handle">@maplecrest</div></div></li>
    <li class="suggest-item"><i class="suggest-mark"></i><div><div class="suggest-name">Corvane Digest <svg width="11" height="11" viewBox="0 0 20 20"><circle cx="10" cy="10" r="10" fill="var(--blue)"/><path d="M5.5 10l3 3 6-6" stroke="#fff" stroke-width="2.5" fill="none"/></svg></div><div class="suggest-handle">@corvanedigest</div></div></li>
  </ul>
</aside>

<aside class="video-card" style="top:1043px">
  <div class="video-thumb" role="img" aria-label="Video still: raised hands holding signs and phones in front of a brick wall" style="background:linear-gradient(135deg,#d8d6d0,#8ca4a8 50%,#c9b69a)">
    <svg width="54" height="54" viewBox="0 0 54 54"><circle cx="27" cy="27" r="25" stroke="#fff" stroke-width="3" fill="none"/><path d="M21 16l17 11-17 11z" fill="#fff"/></svg>
  </div>
  <p>It is a long established fact that a reader will be distracted by the readable content of a page when looking at its layout <a>[......]</a></p>
</aside>

<aside class="video-card" style="top:1326px">
  <div class="video-thumb" role="img" aria-label="Video still: illustrated laptop surrounded by social media icons on teal" style="background:linear-gradient(135deg,#2a6f7e,#3f9aa6 50%,#e88a3a)">
    <svg width="54" height="54" viewBox="0 0 54 54"><circle cx="27" cy="27" r="25" stroke="#fff" stroke-width="3" fill="none"/><path d="M21 16l17 11-17 11z" fill="#fff"/></svg>
  </div>
  <p>It is a long established fact that a reader will be distracted by the readable content of a page when looking at its layout <a>[......]</a></p>
</aside>

<footer class="site-footer">
  <p class="copyright">© Copy Rights 2015 Teamvale.all Right Reserved.</p>
  <div class="footer-social">
    <i class="social-circle" aria-label="Social link one"></i>
    <i class="social-circle" aria-label="Social link two"></i>
    <i class="social-circle" aria-label="Video channel"></i>
    <i class="social-circle" aria-label="Social link four"></i>
  </div>
  <span class="footer-code">C2</span>
</footer>

</body>
</html>
```